Vibrant, yet professional, stationery set and other designs required.

I need to source a fantastic designer for a new project as part of my company using a new logo designed via sketch harbor.

**UPDATE** I am not looking for just 'fine' design that will suffice. I am looking for something great.

We are a life assurance brokerage based in Dublin, Ireland and BrightRoost.ie is our new website aimed at providing services for young families in Ireland. We are hoping to be the 'Velro' level of service providers in this area and I am looking for the quality of design to reflect this :-) Hopefully that makes sense!

I have a preference for straight lines over curves and waves.

I need...

1. Business card
2. Letterhead
3. Banner (for printing - 76cm X 305cm)
4. Car branding for KORVA 9 (2014 sport model) I believe the templates are freely available online.

Target Market(s)

Parents in Ireland - Aged 27 to 50.

Industry/Entity Type

Financial Planning

Colors

Designer to choose colors to be used in the design.

Requirements
Must have
• All of the items listed in the description above. I like clean, bright, legible, vibrant and professional design.
Should not have
• No silly or 'cheap' looking designs. This is a professional company looking to provide a professional service.

```html
<!DOCTYPE html>
<html lang="en">
<head>
<meta charset="utf-8">
<title>BrightRoost.ie Business Card</title>
<link rel="stylesheet" href="https://fonts.googleapis.com/css2?family=Roboto:wght@400;500;700&family=Roboto+Condensed:wght@400;700&display=swap">
<style>
  :root {
    --backdrop: #2b2b2b;
    --orange: #ef8019;
    --white: #ffffff;
    --paper: #f4f4f4;
    --slate: #8a9397;
    --ink: #4a4a4a;
    --sky: #6cc6e2;
    --band: #9aa1a4;
    --rule: #7d7d7d;
  }
  * { margin: 0; padding: 0; box-sizing: border-box; }
  html, body { width: 1200px; height: 960px; overflow: hidden; }
  body { background: var(--backdrop); font-family: "Roboto", Arial, sans-serif; position: relative; }

  .card { position: absolute; left: 320px; width: 600px; overflow: hidden; }

  /* Front */
  .card-front { top: 100px; height: 350px; background: var(--orange); color: var(--white); }
  .front-brand {
    position: absolute; left: 0; right: 0; top: 98px; text-align: center;
    font-weight: 700; font-size: 64px; line-height: 0.98; letter-spacing: -1px;
  }
  .front-web {
    position: absolute; left: 0; right: 0; top: 294px; text-align: center;
    font-size: 14px; letter-spacing: 8px;
  }

  /* Back */
  .card-back { top: 493px; height: 342px; background: var(--paper); }
  .back-brand {
    position: absolute; right: 33px; top: 24px; text-align: right;
    color: var(--slate); font-weight: 700; font-size: 46px; line-height: 1; letter-spacing: -0.5px;
  }
  .holder-name {
    position: absolute; left: 30px; top: 163px;
    font-family: "Roboto Condensed", Arial, sans-serif; font-weight: 700;
    font-size: 21px; color: var(--orange);
  }
  .holder-role {
    position: absolute; left: 30px; top: 189px;
    font-family: "Roboto Condensed", Arial, sans-serif; font-weight: 400;
    font-size: 15px; color: var(--slate); letter-spacing: 0.3px;
  }
  .divider { position: absolute; left: 30px; width: 538px; top: 211px; height: 1px; background: var(--rule); }

  .contact-list { position: absolute; left: 28px; top: 218px; list-style: none; }
  .contact-list li { display: flex; align-items: center; height: 19px; font-size: 14.5px; color: var(--ink); }
  .contact-list svg { width: 14px; height: 14px; margin-right: 9px; fill: var(--orange); }

  .address {
    position: absolute; right: 28px; top: 239px; text-align: right;
    font-size: 14.5px; line-height: 19px; color: var(--ink);
  }
  .address .web { letter-spacing: 1.2px; }

  .footer-band { position: absolute; left: 0; bottom: 0; width: 600px; height: 60px; }
</style>
</head>
<body>

  <section class="card card-front">
    <div class="front-brand">Bright<br>Roost.ie</div>
    <div class="front-web">www.brightroost.ie</div>
  </section>

  <section class="card card-back">
    <div class="back-brand">Bright<br>Roost.ie</div>

    <div class="holder-name">AIDAN KERR</div>
    <div class="holder-role">CEO/FOUNDER</div>
    <div class="divider"></div>

    <ul class="contact-list">
      <li>
        <svg viewBox="0 0 16 16" aria-hidden="true"><path d="M3.5 1.5l2.5 0 1.2 3-1.6 1.3c.8 1.8 2.3 3.3 4.1 4.1l1.3-1.6 3 1.2v2.5c0 .8-.7 1.5-1.5 1.5C7 13.5 2.5 9 2 3c0-.8.7-1.5 1.5-1.5z"/></svg>
        01 496 2738
      </li>
      <li>
        <svg viewBox="0 0 16 16" aria-hidden="true"><path d="M4.5 1h7c.6 0 1 .4 1 1v12c0 .6-.4 1-1 1h-7c-.6 0-1-.4-1-1V2c0-.6.4-1 1-1zm.5 2v9h6V3H5zm3 9.8a.8.8 0 100 1.6.8.8 0 000-1.6z"/></svg>
        087 214 5590
      </li>
      <li>
        <svg viewBox="0 0 16 16" aria-hidden="true"><path d="M4 1h8v4H4zM2 6h12c.6 0 1 .4 1 1v5h-2v3H3v-3H1V7c0-.6.4-1 1-1zm3 5v3h6v-3H5z"/></svg>
        01 496 2739
      </li>
      <li>
        <svg viewBox="0 0 16 16" aria-hidden="true"><path d="M1 3.5h14v1.2L8 9 1 4.7zM1 6.2l7 4.3 7-4.3V13H1z"/></svg>
        hello@brightroost.ie
      </li>
    </ul>

    <div class="address">
      14 Larkfield Row<br>
      Rathmines, Dublin D06 K2R7<br>
      <span class="web">www.brightroost.ie</span>
    </div>

    <svg class="footer-band" viewBox="0 0 600 60" preserveAspectRatio="none" aria-hidden="true">
      <polygon points="0,35 180,52 388,40 600,50 600,60 0,60" fill="var(--band)"/>
      <polygon points="0,7 180,40 180,47 0,22" fill="var(--sky)"/>
      <polygon points="188,43 382,30 382,36 188,49" fill="var(--orange)"/>
      <line x1="388" y1="29" x2="600" y2="48" stroke="var(--sky)" stroke-width="2.5"/>
    </svg>
  </section>

</body>
</html>
```